Medical Software Informational Flyer and Website Design

Our company, Copper Fern Systems, is launching a new product, the CFS Clinic Workflow Hub. It is a software suite that will increase the productivity and volume of a LASIK practice.

We want this flyer to be a companion to our big reveal presentation at VEG and BLUDO; it's primary purpose is to inform potential clients on the many ways this software will help their practice. It is also obviously a promotional material. Because it is a companion to our presentation, we feel that it is acceptable for the flyer to contain much more text than would normally be reasonable in a flyer; it will go into more detail about the 12 major selling points of our software than our presentation time will allow. Having said that, however, we still want there to be "breathing room" for the design and the viewer's eyes.

We have uploaded our logo, both in full color and in white with no background (often used for watermarks, but certainly not restricted for that use alone). Our logo should be accompanied by either "Copper Fern Systems" or "CFS" using the Trajan Pro font (unoriginal, we know, but it's what we've chosen). We have included a color palette that compliments our logo, but designs are not limited to that palette (for example, we have found a pink (#cc1448) that compliments the palette and that we have used in the presentation).

We have also uploaded a PSD that includes icons that could compliment 9 of the 12 major selling points for the CFS Clinic Workflow Hub software (the category titles are subject to change). The icons are not necessarily set in stone. For consistency with our presentation, the Protection, Integration, and Review icons should be used, but any of the remaining six (in particular, the Personalized icon) can be changed to whatever you think might be more suitable. The PSD also has some preliminary text for a few of the 12 selling points (we are refining the text now and will get the final content to designers very soon). Also note that the font is simply a placeholder; use whatever font you think would best compliment your design. Finally, keep in mind that the PSD does NOT reflect a design we are looking for; in fact, we hate this "design" and hesitate to call it a design. It was simply a way to arrange the elements to easily distribute them to designers.

We want an 8 1/2in x 11in 8-page flyer that is professional, simple, and has a clear message: this product will revolutionize your practice! We of course also need a website design that compliments the flyer design once the flyer design is finalized and chosen.

We will be monitoring this project closely-- please ask any questions you have!
Updates

Target Market(s)

Physicians, technicians, and marketing personnel in the LASIK industry.

Industry/Entity Type

Software

Number of Pages Required

4 page

Font styles to use
Serif
Sans Serif

```html
<!DOCTYPE html>
<html lang="en">
<head>
<meta charset="utf-8">
<title>CFS Clinic Workflow Hub – Flyer Colour Options</title>
<link href="https://fonts.googleapis.com/css2?family=Arimo:wght@400;700&display=swap" rel="stylesheet">
<style>
:root{
  --stage:#8d8d8d;
  --ink-dark:#0f2a24;
  --teal:#138463;
  --heading:#1a7a5a;
  --card:#fffbe0;
  --card-line:#e6ddb0;
  --body-text:#8a8a7a;
  --overlay-text:rgba(84,124,108,.85);
  --gold-ring:#e8d894;
  --gold-line:#d9c47a;
}
*{margin:0;padding:0;box-sizing:border-box}
html,body{width:1200px;height:1098px;overflow:hidden}
body{background:var(--stage);font-family:"Arimo",Arial,sans-serif;position:relative}
.flyer-page{position:absolute;width:559px;height:791px;overflow:hidden}
.flyer-page--gold{left:23px;top:92px;
  background:radial-gradient(ellipse 70% 60% at 50% 52%,#fffbe2 0%,#f6eab0 45%,#d7bd62 80%,#b5973a 100%)}
.flyer-page--teal{left:607px;top:253px;
  background:radial-gradient(ellipse 70% 60% at 50% 52%,#fcfce4 0%,#eaf0c4 42%,#8fb5a0 78%,#2f7674 100%)}
.top-band{position:absolute;left:0;top:0;width:100%;height:24px;background:var(--ink-dark)}
.info-card{position:absolute;left:71px;width:438px;height:172px}
.info-card__tab{position:absolute;left:0;top:0;width:200px;height:26px;background:var(--card);
  clip-path:polygon(0 0,176px 0,200px 100%,0 100%);border-radius:6px 0 0 0}
.info-card__heading{position:absolute;left:27px;top:9px;font-size:12.5px;font-weight:700;color:var(--heading);letter-spacing:.2px}
.info-card__body{position:absolute;left:0;top:22px;width:100%;height:150px;background:var(--card);border-radius:0 6px 6px 6px;
  box-shadow:0 0 18px rgba(255,250,215,.6)}
.info-card__body::before{content:"";position:absolute;inset:7px;border:1px solid var(--card-line)}
.info-card__text{position:absolute;left:27px;top:30px;width:384px;font-size:9.8px;line-height:14.1px;color:var(--body-text)}
.info-card__overlay{position:absolute;left:89px;top:40px;font-size:44px;font-weight:700;color:var(--overlay-text);white-space:nowrap;letter-spacing:-.5px}
.card-1{top:59px}.card-2{top:250px}.card-3{top:440px}
.bottom-band{position:absolute;left:0;top:716px;width:100%;height:75px;background:var(--ink-dark)}
.bottom-band::after{content:"";position:absolute;left:0;top:66px;width:100%;height:3px;background:var(--gold-line)}
.feature-icon{position:absolute;top:644px;width:106px;height:106px;border-radius:50%;
  background:radial-gradient(circle,var(--teal) 0 46px,var(--gold-ring) 47px 53px)}
.feature-icon svg{position:absolute;left:23px;top:23px;width:60px;height:60px}
.icon-1{left:66px}.icon-2{left:226px}.icon-3{left:387px}
.brand-mark{position:absolute;left:505px;top:732px;width:36px;height:36px;border:2px solid #fff;background:var(--ink-dark);
  color:#fff;font-size:11px;font-weight:700;display:flex;align-items:center;justify-content:center}
</style>
</head>
<body>

<section class="flyer-page flyer-page--gold">
  <div class="top-band"></div>

  <article class="info-card card-1">
    <div class="info-card__tab"></div><div class="info-card__body"></div>
    <h2 class="info-card__heading">REVIEWS</h2>
    <p class="info-card__text">It's time for a revolution in an industry that depends on effective marketing, tracking marketing campaign effectiveness &amp; converting interest into procedures. Finally comes the solution: the CFS Clinic Workflow Hub which includes connectivity between your marketing records &amp; your patient records. Two databases, one for patients &amp; one for prospective patients, with a single program connecting them. It's simple, it's HIPAA-compliant &amp; it's only the beginning.</p>
    <div class="info-card__overlay">Dumy Text</div>
  </article>

  <article class="info-card card-2">
    <div class="info-card__tab"></div><div class="info-card__body"></div>
    <h2 class="info-card__heading">PLANNING TOOLS</h2>
    <p class="info-card__text">It's time for a revolution in an industry that depends on effective marketing, tracking marketing campaign effectiveness &amp; converting interest into procedures. Finally comes the solution: the CFS Clinic Workflow Hub which includes connectivity between your marketing records &amp; your patient records. Two databases, one for patients &amp; one for prospective patients, with a single program connecting them. It's simple, it's HIPAA-compliant &amp; it's only the beginning.</p>
    <div class="info-card__overlay">Dumy Text</div>
  </article>

  <article class="info-card card-3">
    <div class="info-card__tab"></div><div class="info-card__body"></div>
    <h2 class="info-card__heading">IMPROVEMENT TOOLS</h2>
    <p class="info-card__text">It's time for a revolution in an industry that depends on effective marketing, tracking marketing campaign effectiveness &amp; converting interest into procedures. Finally comes the solution: the CFS Clinic Workflow Hub which includes connectivity between your marketing records &amp; your patient records. Two databases, one for patients &amp; one for prospective patients, with a single program connecting them. It's simple, it's HIPAA-compliant &amp; it's only the beginning.</p>
    <div class="info-card__overlay">Dumy Text</div>
  </article>

  <div class="bottom-band"></div>
  <div class="feature-icon icon-1"><svg viewBox="0 0 60 60"><polygon points="26,6 32,21 48,22 35,32 40,48 26,39 12,48 17,32 4,22 20,21" fill="#fffbe6"/><polygon points="40,10 44,19 54,20 46,26 49,36 40,30 33,35 35,26 30,20 37,19" fill="#a8dcc6"/></svg></div>
  <div class="feature-icon icon-2"><svg viewBox="0 0 60 60"><rect x="12" y="8" width="32" height="44" rx="2" fill="#fffbe6"/><rect x="21" y="5" width="14" height="7" rx="2" fill="#fffbe6" stroke="#138463" stroke-width="1.5"/><g stroke="#138463" stroke-width="2.5"><line x1="18" y1="20" x2="38" y2="20"/><line x1="18" y1="27" x2="38" y2="27"/><line x1="18" y1="34" x2="38" y2="34"/><line x1="18" y1="41" x2="30" y2="41"/></g><path d="M34 52 L50 30 L54 33 L38 55 L33 56 Z" fill="#fffbe6" stroke="#138463" stroke-width="1.5"/></svg></div>
  <div class="feature-icon icon-3"><svg viewBox="0 0 60 60"><g fill="none" stroke="#fffbe6" stroke-width="6" stroke-linejoin="miter"><polyline points="8,32 30,14 52,32"/><polyline points="8,44 30,26 52,44"/><polyline points="8,56 30,38 52,56"/></g></svg></div>
  <div class="brand-mark">CFS</div>
</section>

<section class="flyer-page flyer-page--teal">
  <div class="top-band"></div>

  <article class="info-card card-1">
    <div class="info-card__tab"></div><div class="info-card__body"></div>
    <h2 class="info-card__heading">HEADING HERE</h2>
    <p class="info-card__text">It's time for a revolution in an industry that depends on effective marketing, tracking marketing campaign effectiveness &amp; converting interest into procedures. Finally comes the solution: the CFS Clinic Workflow Hub which includes connectivity between your marketing records &amp; your patient records. Two databases, one for patients &amp; one for prospective patients, with a single program connecting them. It's simple, it's HIPAA-compliant &amp; it's only the beginning.</p>
    <div class="info-card__overlay">Dumy Text</div>
  </article>

  <article class="info-card card-2">
    <div class="info-card__tab"></div><div class="info-card__body"></div>
    <h2 class="info-card__heading">HEADING HERE</h2>
    <p class="info-card__text">It's time for a revolution in an industry that depends on effective marketing, tracking marketing campaign effectiveness &amp; converting interest into procedures. Finally comes the solution: the CFS Clinic Workflow Hub which includes connectivity between your marketing records &amp; your patient records. Two databases, one for patients &amp; one for prospective patients, with a single program connecting them. It's simple, it's HIPAA-compliant &amp; it's only the beginning.</p>
    <div class="info-card__overlay">Dumy Text</div>
  </article>

  <article class="info-card card-3">
    <div class="info-card__tab"></div><div class="info-card__body"></div>
    <h2 class="info-card__heading">HEADING HERE</h2>
    <p class="info-card__text">It's time for a revolution in an industry that depends on effective marketing, tracking marketing campaign effectiveness &amp; converting interest into procedures. Finally comes the solution: the CFS Clinic Workflow Hub which includes connectivity between your marketing records &amp; your patient records. Two databases, one for patients &amp; one for prospective patients, with a single program connecting them. It's simple, it's HIPAA-compliant &amp; it's only the beginning.</p>
    <div class="info-card__overlay">Dumy Text</div>
  </article>

  <div class="bottom-band"></div>
  <div class="feature-icon icon-1"><svg viewBox="0 0 60 60"><path d="M30 4 C22 10 14 11 8 10 C8 32 14 46 30 56 C46 46 52 32 52 10 C46 11 38 10 30 4 Z" fill="#fffbe6"/><path d="M30 10 C24 14 18 15 13 15 C14 32 19 42 30 50 C41 42 46 32 47 15 C42 15 36 14 30 10 Z" fill="#5cc4a0"/></svg></div>
  <div class="feature-icon icon-2"><svg viewBox="0 0 60 60"><g fill="#fffbe6"><rect x="6" y="44" width="7" height="10"/><rect x="16" y="38" width="7" height="16"/><rect x="26" y="32" width="7" height="22"/><rect x="36" y="26" width="7" height="28"/><rect x="46" y="20" width="7" height="34"/></g><path d="M6 38 C22 34 34 24 44 12" fill="none" stroke="#fffbe6" stroke-width="3"/><polygon points="38,10 52,4 48,18" fill="#fffbe6"/></svg></div>
  <div class="feature-icon icon-3"><svg viewBox="0 0 60 60"><path d="M30 6 A24 24 0 1 0 54 34 L42 34 A8 8 0 0 1 34 26 Z" fill="#fffbe6"/></svg></div>
  <div class="brand-mark">CFS</div>
</section>

</body>
</html>
```